Belmont Ridge Business Card Design Project

We have recently rebranded and would like to design new business cards that incorporate the corporate logo - double sided cards with corporate logo on one side and contact details on the other

Target Market(s)

Sophisticated and high net worth investors and finance industry professionals

Industry/Entity Type

Funds Management

Contact Information for Business Card

The card should prominently feature the company name and logo. Other details will be standard contact details for each staff member - name, address, phone, email, website

Colors
0054AA
0677BA
7BADD7
CADEEF
E8F1F8

Requirements
Must have
• Double-sided design with one side prominently featuring the corporate logo and the other side with all standard contact details

```html
<!DOCTYPE html>
<html lang="en">
<head>
<meta charset="utf-8">
<title>Belmont Ridge — Business Card</title>
<link rel="stylesheet" href="https://fonts.googleapis.com/css2?family=Cinzel:wght@400;600&family=Arimo:wght@400;700&display=swap">
<style>
  :root {
    --backdrop: #e4e4e2;
    --card-navy: #21477a;
    --card-deep: #163762;
    --card-mid: #2b5590;
    --ink-light: #ffffff;
    --ink-soft: #dfe8f3;
    --accent: #4a86c8;
  }
  * { box-sizing: border-box; margin: 0; padding: 0; }
  html, body { width: 1200px; height: 802px; overflow: hidden; }
  body {
    background: var(--backdrop);
    font-family: "Arimo", Arial, sans-serif;
    position: relative;
  }
  .card {
    position: absolute;
    top: 236px;
    width: 520px;
    height: 300px;
    background: var(--card-navy);
    color: var(--ink-light);
    box-shadow: 0 6px 18px rgba(0,0,0,0.18);
    overflow: hidden;
  }
  .card--front { left: 50px; }
  .card--back { left: 630px; }

  .brand {
    display: flex;
    align-items: center;
    justify-content: center;
    gap: 14px;
  }
  .brand__mark {
    flex: none;
    border-radius: 50%;
    background: var(--ink-light);
  }
  .brand-name {
    font-family: "Cinzel", Georgia, serif;
    font-weight: 400;
    letter-spacing: 1px;
    color: var(--ink-light);
    white-space: nowrap;
  }

  .card--front .brand {
    position: absolute;
    top: 48px;
    left: 0;
    width: 100%;
  }
  .card--front .brand__mark { width: 26px; height: 26px; }
  .card--front .brand-name { font-size: 32px; }

  .contact-block {
    position: absolute;
    top: 140px;
    left: 0;
    width: 100%;
    display: flex;
    justify-content: center;
    align-items: center;
  }
  .person { text-align: right; padding-right: 18px; }
  .person__name {
    font-weight: 700;
    font-size: 19px;
    letter-spacing: 0.5px;
    text-transform: uppercase;
  }
  .person__role { font-size: 13px; color: var(--ink-soft); margin-top: 3px; }
  .divider { width: 1px; height: 70px; background: var(--ink-light); }
  .details {
    list-style: none;
    padding-left: 18px;
    font-size: 13.5px;
    line-height: 22px;
  }
  .details li { display: flex; align-items: center; gap: 8px; }
  .details svg { width: 12px; height: 12px; flex: none; }
  .address {
    position: absolute;
    bottom: 46px;
    left: 0;
    width: 100%;
    text-align: center;
    font-size: 13.5px;
    color: var(--ink-soft);
  }

  .card--back .brand {
    position: absolute;
    top: 40px;
    left: 0;
    width: 100%;
  }
  .card--back .brand__mark { width: 30px; height: 30px; background: #e9eef5; }
  .card--back .brand-name { font-size: 38px; color: #e9eef5; }

  .decor-area {
    position: absolute;
    left: 0;
    right: 0;
    bottom: 0;
    height: 175px;
    background:
      linear-gradient(100deg, var(--card-deep) 0%, var(--card-mid) 55%, var(--accent) 100%);
    opacity: 0.9;
  }
</style>
</head>
<body>

  <section class="card card--front" aria-label="Business card, contact side">
    <div class="brand">
      <span class="brand__mark" aria-hidden="true"></span>
      <h1 class="brand-name">Belmont Ridge</h1>
    </div>

    <div class="contact-block">
      <div class="person">
        <p class="person__name">Daniel Whitford</p>
        <p class="person__role">Manager</p>
      </div>
      <span class="divider"></span>
      <ul class="details">
        <li>
          <svg viewBox="0 0 12 12" aria-hidden="true"><circle cx="6" cy="6" r="6" fill="#fff"/><path d="M3.6 3.2l1.3-.4.7 1.5-.8.6c.4.8 1 1.4 1.8 1.8l.6-.8 1.5.7-.4 1.3C6 7.8 4.2 6 3.6 3.2z" fill="#21477a"/></svg>
          <span>555-014-2100</span>
        </li>
        <li>
          <svg viewBox="0 0 12 12" aria-hidden="true"><rect x="0.5" y="2.5" width="11" height="7" fill="#fff"/><path d="M0.5 2.5L6 6.6l5.5-4.1" fill="none" stroke="#21477a" stroke-width="1"/></svg>
          <span>daniel@belmontridge.com</span>
        </li>
        <li>
          <svg viewBox="0 0 12 12" aria-hidden="true"><circle cx="6" cy="6" r="6" fill="#fff"/><circle cx="6" cy="6" r="3.2" fill="none" stroke="#21477a" stroke-width="1"/><path d="M2.8 6h6.4M6 2.8v6.4" stroke="#21477a" stroke-width="0.8"/></svg>
          <span>www.belmontridge.com</span>
        </li>
      </ul>
    </div>

    <p class="address">Your Address, City, State, Zip 0000</p>
  </section>

  <section class="card card--back" aria-label="Business card, brand side">
    <div class="brand">
      <span class="brand__mark" aria-hidden="true"></span>
      <h2 class="brand-name">Belmont Ridge</h2>
    </div>
    <div class="decor-area" role="img" aria-label="Large brand graphic in layered navy and light blue tones"></div>
  </section>

</body>
</html>
```